New Business Card Design Project

Need a design that will create an impact / strong impression towards our clients for our business. We are in the lighting business and we do lighting retrofits for large commercial to industrial clientele.

Target Market(s)

Lighting Industry

Industry/Entity Type

Business

Font styles to use
Other font styles liked:
• we would like to use the font on our logo, not sure what it is though..

Requirements
Must have
• Our logo.
Nice to have
• We are open to suggestions that have to do with lighting.

```html
<!DOCTYPE html>
<html lang="en">
<head>
<meta charset="utf-8">
<title>Brightline Retrofit Group – Business Card</title>
<link rel="stylesheet" href="https://fonts.googleapis.com/css2?family=Roboto+Condensed:wght@400;700&family=Roboto:wght@400;500&display=swap">
<style>
  :root {
    --backdrop: #e9e7e2;
    --card-white: #f7f7f5;
    --brand-green: #134d16;
    --accent-green: #2f8f3a;
    --text-grey: #5a5a5a;
    --white: #ffffff;
  }
  * { margin: 0; padding: 0; box-sizing: border-box; }
  html, body {
    width: 1200px; height: 911px; overflow: hidden;
    background: var(--backdrop);
    font-family: "Roboto", Arial, sans-serif;
  }
  .stage { position: relative; width: 1200px; height: 911px; }

  .card {
    position: absolute;
    width: 560px; height: 320px;
    border-radius: 18px;
    box-shadow: 0 10px 28px rgba(0,0,0,.18);
    overflow: hidden;
  }

  /* front */
  .card--front { left: 60px; top: 110px; background: var(--card-white); }
  .front-rule {
    position: absolute; top: 0; bottom: 0; right: 22px;
    width: 3px; background: var(--brand-green);
  }
  .brand {
    position: absolute; display: flex; align-items: center; gap: 12px;
    font-family: "Roboto Condensed", Arial, sans-serif;
    font-weight: 700; text-transform: uppercase; line-height: 1.05;
  }
  .brand__mark { width: 30px; height: 30px; flex: none; }
  .card--front .brand { left: 40px; top: 128px; color: var(--brand-green); font-size: 24px; width: 230px; }
  .card--front .brand__mark { background: var(--accent-green); }

  .contact-block { position: absolute; left: 300px; top: 40px; width: 220px; }
  .person__name {
    font-family: "Roboto Condensed", Arial, sans-serif;
    font-weight: 700; font-size: 24px; color: var(--brand-green);
    letter-spacing: .5px;
  }
  .person__title {
    font-family: "Roboto Condensed", Arial, sans-serif;
    font-size: 16px; color: var(--accent-green); margin-top: 2px;
    padding-bottom: 10px; border-bottom: 2px solid var(--brand-green);
  }
  .address { font-size: 13px; color: var(--text-grey); line-height: 1.45; margin-top: 14px; }
  .contact-list { list-style: none; margin-top: 14px; }
  .contact-list li {
    display: flex; align-items: center; gap: 9px;
    font-size: 13px; color: var(--text-grey); line-height: 1.75;
  }
  .contact-list svg { width: 13px; height: 13px; flex: none; }

  /* back */
  .card--back { left: 580px; top: 470px; background: var(--brand-green); }
  .back-url {
    position: absolute; left: 0; right: 0; top: 28px; text-align: center;
    font-size: 13px; letter-spacing: 2.5px; color: var(--white);
  }
  .card--back .brand {
    left: 50%; top: 50%; transform: translate(-50%, -50%);
    color: var(--white); font-size: 34px; white-space: nowrap;
  }
  .card--back .brand__mark { width: 40px; height: 40px; background: var(--white); }
</style>
</head>
<body>
<div class="stage">

  <section class="card card--front" aria-label="Business card front">
    <div class="brand">
      <span class="brand__mark"></span>
      <span class="brand__name">Brightline Retrofit Group, LLC</span>
    </div>

    <div class="contact-block">
      <p class="person__name">DANIEL REYES</p>
      <p class="person__title">CEO/FOUNDER</p>
      <p class="address">1420 Birchwood Avenue<br>Fairbanks, Alaska 99701</p>
      <ul class="contact-list">
        <li>
          <svg viewBox="0 0 16 16"><path fill="#134d16" d="M3 1l3 .5 1 3.5-2 1.5a9 9 0 0 0 4.5 4.5l1.5-2 3.5 1 .5 3-2 2C6 15 1 10 1 3z"/></svg>
          555 214 7730
        </li>
        <li>
          <svg viewBox="0 0 16 16"><rect x="4" y="1" width="8" height="14" rx="1.5" fill="none" stroke="#134d16" stroke-width="1.8"/><circle cx="8" cy="12.3" r="1" fill="#134d16"/></svg>
          555 389 1062
        </li>
        <li>
          <svg viewBox="0 0 16 16"><rect x="1" y="5" width="14" height="9" rx="1" fill="#134d16"/><rect x="4" y="1" width="8" height="5" fill="none" stroke="#134d16" stroke-width="1.6"/></svg>
          555 671 4485
        </li>
        <li>
          <svg viewBox="0 0 16 16"><rect x="1" y="3" width="14" height="10" rx="1" fill="#134d16"/><path d="M2 4l6 5 6-5" fill="none" stroke="#f7f7f5" stroke-width="1.4"/></svg>
          daniel@brightlinegroup.com
        </li>
        <li>
          <svg viewBox="0 0 16 16"><circle cx="8" cy="8" r="7" fill="#134d16"/><path d="M1 8h14M8 1c-3 3.5-3 10.5 0 14M8 1c3 3.5 3 10.5 0 14" fill="none" stroke="#f7f7f5" stroke-width="1"/></svg>
          www.brightlinegroup.com
        </li>
      </ul>
    </div>
    <div class="front-rule"></div>
  </section>

  <section class="card card--back" aria-label="Business card back">
    <p class="back-url">www.brightlineretrofitgroup.com</p>
    <div class="brand">
      <span class="brand__mark"></span>
      <span class="brand__name">Brightline Retrofit Group</span>
    </div>
  </section>

</div>
</body>
</html>
```